Business Card Design

We need a business card designed for our new company. Prefer a black card with white logo & writing.

Contact Information for Business Card

Ted Galloway, address: 7-4812 Fernhollow Road, Abbotsford, BC, V3K 8R2, Office Phone: 604-712-3390, Cell: 604-947-2164, Email: ted@resinworkshub.ca

Colors

Designer to choose only greyscale colors for use in the design.

```html
<!DOCTYPE html>
<html lang="en">
<head>
<meta charset="utf-8">
<title>Resin Works Hub – Business Card</title>
<link href="https://fonts.googleapis.com/css2?family=Poppins:wght@300;400;700&display=swap" rel="stylesheet">
<style>
  :root {
    --backdrop: #202022;
    --card: #1b1b1d;
    --ink: #f4f4f4;
    --ink-soft: #cfcfcf;
    --grey-dark: #2a2a2c;
    --grey-mid: #5a5a5c;
    --grey-light: #a8a8aa;
  }
  * { box-sizing: border-box; margin: 0; padding: 0; }
  html, body { width: 1200px; height: 780px; overflow: hidden; }
  body {
    background: var(--backdrop);
    font-family: "Poppins", sans-serif;
    color: var(--ink);
    position: relative;
  }
  .card {
    position: absolute;
    top: 92px;
    width: 340px;
    height: 595px;
    background: var(--card);
    border-radius: 4px;
    box-shadow: 0 10px 30px rgba(0,0,0,.55);
    overflow: hidden;
  }
  .card--front { left: 220px; }
  .card--back  { left: 640px; }

  .brand {
    font-weight: 700;
    text-transform: uppercase;
    color: var(--ink);
    display: flex;
    align-items: center;
    gap: 10px;
    line-height: 1.05;
  }
  .brand__mark {
    width: 14px; height: 14px;
    background: var(--ink);
    flex: none;
  }
  .card--front .brand {
    position: absolute;
    top: 52px; left: 0; right: 0;
    justify-content: center;
    font-size: 26px;
  }

  .contact {
    position: absolute;
    top: 130px; left: 40px;
    font-size: 13px;
    font-weight: 300;
    color: var(--ink-soft);
    line-height: 1.55;
  }
  .contact__address { margin-bottom: 10px; }
  .contact__list { list-style: none; }
  .contact__item { display: flex; align-items: center; gap: 9px; }
  .contact__icon { width: 12px; height: 12px; flex: none; }

  .peak-art {
    position: absolute;
    left: 0; right: 0; bottom: 0;
    height: 250px;
    background: linear-gradient(160deg, transparent 30%, var(--grey-dark) 55%, var(--grey-mid) 72%, var(--card) 95%);
  }
  .holder {
    position: absolute;
    right: 34px; bottom: 60px;
    text-align: right;
  }
  .holder__name {
    font-size: 34px;
    font-weight: 300;
    line-height: 1.1;
  }
  .holder__first { font-weight: 700; }
  .holder__role {
    font-size: 18px;
    font-weight: 300;
    color: var(--ink-soft);
  }

  .pattern {
    position: absolute;
    inset: 0;
    background: linear-gradient(135deg, var(--grey-dark), var(--card) 45%, var(--grey-dark) 75%, var(--grey-mid));
  }
  .card--back .brand {
    position: absolute;
    top: 0; bottom: 0; left: 0; right: 0;
    justify-content: center;
    font-size: 30px;
  }
</style>
</head>
<body>
  <section class="card card--front">
    <div class="brand"><span class="brand__mark"></span>Resin Works Hub</div>

    <div class="contact">
      <p class="contact__address">7-4812 Fernhollow Road,<br>Abbotsford, BC, V3K 8R2.</p>
      <ul class="contact__list">
        <li class="contact__item">
          <svg class="contact__icon" viewBox="0 0 12 12"><path d="M2 1h2.5l1 3-1.5 1a7 7 0 0 0 3 3l1-1.5 3 1V10a1 1 0 0 1-1 1A10 10 0 0 1 1 2a1 1 0 0 1 1-1z" fill="var(--ink)"/></svg>
          604-712-3390
        </li>
        <li class="contact__item">
          <svg class="contact__icon" viewBox="0 0 12 12"><rect x="3" y="0.5" width="6" height="11" rx="1" fill="none" stroke="var(--ink)"/><circle cx="6" cy="9.5" r=".8" fill="var(--ink)"/></svg>
          604-947-2164
        </li>
        <li class="contact__item">
          <svg class="contact__icon" viewBox="0 0 12 12"><circle cx="6" cy="6" r="5.2" fill="none" stroke="var(--ink)"/><ellipse cx="6" cy="6" rx="2.2" ry="5.2" fill="none" stroke="var(--ink)"/><line x1="0.8" y1="6" x2="11.2" y2="6" stroke="var(--ink)"/></svg>
          www.resinworkshub.ca
        </li>
        <li class="contact__item">
          <svg class="contact__icon" viewBox="0 0 12 12"><rect x="0.5" y="2.5" width="11" height="7" fill="none" stroke="var(--ink)"/><path d="M0.5 2.5 6 7l5.5-4.5" fill="none" stroke="var(--ink)"/></svg>
          ted@resinworkshub.ca
        </li>
      </ul>
    </div>

    <div class="peak-art" role="img" aria-label="Silver mountain peak illustration sweeping across the lower card"></div>

    <div class="holder">
      <p class="holder__name"><span class="holder__first">Ted</span> Galloway</p>
      <p class="holder__role">owner</p>
    </div>
  </section>

  <section class="card card--back">
    <div class="pattern" role="img" aria-label="Repeating embossed mountain-ridge chevron pattern in black and silver"></div>
    <div class="brand"><span class="brand__mark"></span>Resin Works Hub</div>
  </section>
</body>
</html>
```